Business Card Design

We are a commercial real estate brokerage in San Francisco, leasing office buildings downtown.
I would like a clean, elegant look. Simple but powerful .

Industry/Entity Type

Business

Contact Information for Business Card

Derek Holloway
lic# 07258143
415.555.0172
derek@velt-commercial.example
velt-commercial.example

```html
<!DOCTYPE html>
<html lang="en">
<head>
<meta charset="utf-8">
<title>Velt Commercial – Business Card</title>
<link rel="stylesheet" href="https://fonts.googleapis.com/css2?family=Source+Sans+3:wght@400;600;700&display=swap">
<style>
  :root {
    --backdrop: #141414;
    --card-front: #f3f3f3;
    --card-back: #7789a6;
    --accent: #6e809e;
    --ink: #111111;
    --ink-soft: #4a4a4a;
    --white: #ffffff;
  }
  * { margin: 0; padding: 0; box-sizing: border-box; }
  html, body {
    width: 1200px; height: 900px; overflow: hidden;
    background: var(--backdrop);
    font-family: "Source Sans 3", "Helvetica Neue", Arial, sans-serif;
  }
  .stage { position: relative; width: 1200px; height: 900px; }
  .card {
    position: absolute; top: 184px; height: 490px;
    border-radius: 12px; overflow: hidden;
  }
  .card--front { left: 299px; width: 301px; background: var(--card-front); }
  .card--back  { left: 645px; width: 304px; background: var(--card-back); }

  .front-brand {
    position: absolute; top: 62px; left: 0; right: 0;
    display: flex; align-items: center; justify-content: center; gap: 12px;
  }
  .front-brand__mark {
    width: 14px; height: 14px; background: var(--accent);
  }
  .front-brand__name {
    color: var(--accent); font-weight: 700; line-height: 1;
    text-align: left; letter-spacing: 0.5px;
  }
  .front-brand__name .line1 { display: block; font-size: 42px; }
  .front-brand__name .line2 { display: block; font-size: 20px; margin-top: 2px; letter-spacing: 0.8px; }

  .agent-name {
    position: absolute; top: 286px; left: 0; right: 0; text-align: center;
    color: var(--accent); font-weight: 600; font-size: 19px; letter-spacing: 0.4px;
  }
  .license {
    position: absolute; top: 341px; left: 0; right: 0; text-align: center;
    font-size: 14px; font-weight: 700; color: var(--ink);
  }
  .license__label { color: var(--accent); }

  .contact {
    position: absolute; top: 396px; left: 0; right: 0;
    list-style: none; text-align: center;
    font-size: 14px; color: var(--ink); line-height: 20.5px;
  }
  .contact svg { width: 10px; height: 10px; vertical-align: -1px; margin-right: 3px; fill: var(--accent); }

  .back-brand {
    position: absolute; top: 44px; left: 0; right: 0; text-align: center;
    color: var(--white); font-weight: 700; line-height: 1;
  }
  .back-brand .line1 { display: block; font-size: 62px; letter-spacing: 1px; }
  .back-brand .line2 { display: block; font-size: 27px; letter-spacing: 1px; margin-top: 0; }
</style>
</head>
<body>
<main class="stage">
  <section class="card card--front" aria-label="Business card front">
    <div class="front-brand">
      <span class="front-brand__mark" aria-hidden="true"></span>
      <div class="front-brand__name">
        <span class="line1">VELT</span>
        <span class="line2">COMMERCIAL</span>
      </div>
    </div>
    <p class="agent-name">DEREK HOLLOWAY</p>
    <p class="license"><span class="license__label">Lic#</span> 07258143</p>
    <ul class="contact">
      <li><svg viewBox="0 0 10 10"><path d="M2 0.5 L3.6 2.6 L2.8 3.6 Q4 6 6.4 7.2 L7.4 6.4 L9.5 8 L8.4 9.5 Q1 8 0.5 1.6 Z"/></svg>415.555.0172</li>
      <li><svg viewBox="0 0 10 10"><path d="M0 2 H10 V8.5 H0 Z" /><path d="M0.4 2.3 L5 5.6 L9.6 2.3" stroke="#f3f3f3" stroke-width="0.9" fill="none"/></svg>derek@velt-commercial.example</li>
      <li><svg viewBox="0 0 10 10"><path d="M4.2 5.8 L5.8 4.2" stroke="#6e809e" stroke-width="1.2"/><rect x="0.8" y="4.6" width="4" height="2.6" rx="1.3" transform="rotate(-45 2.8 5.9)" fill="none" stroke="#6e809e" stroke-width="1.1"/><rect x="5.2" y="2.8" width="4" height="2.6" rx="1.3" transform="rotate(-45 7.2 4.1)" fill="none" stroke="#6e809e" stroke-width="1.1"/></svg>velt-commercial.example</li>
    </ul>
  </section>

  <section class="card card--back" aria-label="Business card back">
    <div class="back-brand">
      <span class="line1">VELT</span>
      <span class="line2">COMMERCIAL</span>
    </div>
  </section>
</main>
</body>
</html>
```